Web Design Project

We are looking to for a redesign for www.volketa.com. Volketa Systems is a Managed Service Provider of IT solutions based is Calgary, Alberta, Canada. We are currently expanding into the Edmonton market and would like to lauch our new site with our expansion.
The design should be sleak in style and communicate a professional vision to our clients and prospects.

Thanks,
Dale

Target Market(s)

Small to medium size businesses looking to outsource or complement their IT solutions.

Industry/Entity Type

It Professional

```html
<!DOCTYPE html>
<html lang="en">
<head>
<meta charset="utf-8">
<title>Volketa Systems Inc</title>
<link href="https://fonts.googleapis.com/css2?family=Arimo:wght@400;700&family=Didact+Gothic&family=Fira+Sans+Extra+Condensed:ital,wght@1,600&display=swap" rel="stylesheet">
<style>
:root{
  --topbar:#1f2b36;
  --header:#ffffff;
  --content:#e2e2e2;
  --footer:#c4c4c4;
  --bottom:#1e1e1e;
  --ink:#1a1a1a;
  --body:#444444;
  --rule:#9a9a9a;
  --divider:#eeeeee;
  --accent:#d01f2a;
  --muted:#bdbdbd;
}
*{margin:0;padding:0;box-sizing:border-box}
html,body{width:1040px;height:1200px;overflow:hidden}
body{position:relative;background:var(--content);font-family:"Arimo",Arial,sans-serif;color:var(--body)}
.abs{position:absolute}
.topbar{left:0;top:0;width:1040px;height:3px;background:var(--topbar)}
.header{left:0;top:3px;width:1040px;height:79px;background:var(--header)}
.brand{left:136px;top:27px;display:flex;align-items:center;gap:8px;font-family:"Didact Gothic",sans-serif;font-size:19px;color:var(--ink)}
.brand-mark{width:16px;height:16px;background:var(--accent)}
.nav{left:360px;top:29px;display:flex;font-family:"Didact Gothic",sans-serif;font-size:14px;color:var(--ink)}
.nav span{height:31px;line-height:31px;padding:0 14px;margin-right:1px}
.nav .active{background:linear-gradient(#e8eef2,#c9d5dc);border:1px solid #a9b9c3;border-radius:3px}
.hero{left:0;top:82px;width:1040px;height:324px;background:linear-gradient(100deg,#b9c8cc 0%,#7fa6ab 22%,#2aa3c6 42%,#3a7fd0 50%,#9bd04a 62%,#d8e04c 75%,#9ab84a 90%,#c6d85c 100%)}
.heading{font-family:"Fira Sans Extra Condensed",sans-serif;font-style:italic;font-weight:600;font-size:20px;color:var(--ink)}
.list{list-style:none;width:171px;font-size:10.5px}
.list li{height:25.6px;line-height:24px;padding-left:17px;position:relative;border-bottom:1px dotted var(--rule)}
.list li::before{content:"›";position:absolute;left:3px;top:-1px;font-size:13px;color:var(--ink)}
.list li.current::before{color:var(--accent)}
.photo{border:3px solid #fff}
.subtitle{font-family:"Fira Sans Extra Condensed",sans-serif;font-size:15px;color:var(--ink)}
.para{font-size:10px;line-height:16px;text-align:justify;color:var(--body)}
.rule{left:136px;top:618px;width:768px;border-top:1px dotted var(--rule)}
.svc-title{font-size:10.5px;color:var(--ink)}
.icon{width:32px;height:36px}
.footer{left:0;top:886px;width:1040px;height:208px;background:var(--footer)}
.vline{top:898px;width:1px;height:178px;background:var(--divider)}
.badge{background:#fff;border-radius:3px}
.input{background:#fff;border:1px solid #a8a8a8;border-radius:2px;font-size:10px;color:#666;padding-left:12px;line-height:20px}
.submit{background:#111;color:#fff;font-size:10.5px;text-align:center;line-height:20px;border-radius:2px}
.qlist{list-style:none;width:144px;font-size:10.5px}
.qlist li{height:24px;line-height:22px;padding-left:14px;position:relative;border-bottom:1px dotted #888}
.qlist li::before{content:"›";position:absolute;left:0;top:-1px;font-size:13px;color:var(--ink)}
.qlist li:last-child{border-bottom:none}
.readmore{font-family:"Fira Sans Extra Condensed",sans-serif;font-style:italic;font-size:11px;color:var(--ink)}
.bottom{left:0;top:1094px;width:1040px;height:106px;background:var(--bottom)}
.copy{left:138px;top:1130px;font-size:9.5px;line-height:17px;color:#bbb}
.tollfree{left:700px;width:206px;top:1109px;text-align:right;font-size:15px;color:#ccc}
.social{top:1139px;width:26px;height:27px;background:var(--muted);border-radius:3px}
</style>
</head>
<body>
<div class="abs topbar"></div>
<div class="abs header"></div>
<div class="abs brand"><span class="brand-mark"></span>Volketa Systems Inc</div>
<nav class="abs nav"><span>Home</span><span class="active">About Us</span><span>Solutions</span><span>Careers</span><span>Partners</span><span>Services</span><span>Contact Us</span></nav>
<div class="abs hero" role="img" aria-label="Photo of a metal globe sculpture beside close-up green and yellow keyboard keys"></div>

<div class="abs heading" style="left:136px;top:432px">Company Overview</div>
<ul class="abs list" style="left:137px;top:463px">
  <li class="current">History.</li><li>Company.</li><li>Mission.</li><li>Vision.</li><li>Community.</li>
</ul>

<div class="abs heading" style="left:344px;top:432px">Company info</div>
<div class="abs photo" style="left:344px;top:470px;width:141px;height:125px;background:linear-gradient(135deg,#eef3fb,#9fb5de 60%,#cfdaf0)" role="img" aria-label="Illustration of a computer monitor with a globe"></div>
<div class="abs subtitle" style="left:496px;top:468px">History</div>
<p class="abs para" style="left:496px;top:494px;width:408px">Lorem Ipsum is simply dummy text of the printing and typesetting industry. Lorem Ipsum has been the industry's standard dummy text ever since the 1500s, when an unknown printer took a galley of type and scrambled it to make a type specimen book. It has survived not only five centuries, but also the leap into electronic typesetting, remaining essentially unchanged. It was popularised in the 1960s with the release of Letraset sheets containing Lorem Ipsum passages, and more recently with desktop publishing software like</p>

<div class="abs rule"></div>

<div class="abs heading" style="left:136px;top:635px">Technologies</div>
<ul class="abs list" style="left:137px;top:672px">
  <li>History.</li><li>Company.</li><li>Mission.</li><li>Vision.</li><li>Community.</li><li>Community.</li><li>Community.</li>
</ul>

<div class="abs heading" style="left:344px;top:635px">Service Overview</div>

<svg class="abs icon" style="left:344px;top:684px" viewBox="0 0 32 36" aria-hidden="true"><path d="M4 6 L22 2 L28 6 L28 32 L10 35 L4 32 Z" fill="#9a9a9a"/><path d="M4 6 L10 9 L10 35 L4 32 Z" fill="#6f6f6f"/><path d="M10 9 L28 6 L28 32 L10 35 Z" fill="#b9a88f"/></svg>
<div class="abs svc-title" style="left:380px;top:686px">Software development</div>
<p class="abs para" style="left:380px;top:707px;width:218px">Lorem Ipsum is simply dummy text of the printing and typesetting industry. Lorem Ipsum has been the industry's standard dummy text ever</p>

<svg class="abs icon" style="left:640px;top:682px" viewBox="0 0 32 36" aria-hidden="true"><rect x="2" y="3" width="28" height="22" rx="2" fill="#2c3a44"/><rect x="5" y="6" width="22" height="16" fill="#3ab0e8"/><rect x="13" y="26" width="6" height="4" fill="#777"/><rect x="8" y="30" width="16" height="3" rx="1" fill="#999"/></svg>
<div class="abs svc-title" style="left:685px;top:686px">Planning</div>
<p class="abs para" style="left:685px;top:707px;width:220px">Lorem Ipsum is simply dummy text of the printing and typesetting industry. Lorem Ipsum has been the industry's standard dummy text ever</p>

<svg class="abs icon" style="left:344px;top:762px" viewBox="0 0 32 36" aria-hidden="true"><ellipse cx="16" cy="30" rx="13" ry="4" fill="#8a6a4a"/><rect x="3" y="6" width="26" height="24" fill="#a67c52"/><rect x="3" y="12" width="26" height="5" fill="#3a7fc8"/><rect x="3" y="22" width="26" height="5" fill="#3a7fc8"/><ellipse cx="16" cy="6" rx="13" ry="4" fill="#5aa0e0"/></svg>
<div class="abs svc-title" style="left:380px;top:769px">Delivery</div>
<p class="abs para" style="left:380px;top:795px;width:218px">Lorem Ipsum is simply dummy text of the printing and typesetting industry. Lorem Ipsum has been the industry's standard dummy text ever</p>

<svg class="abs icon" style="left:640px;top:768px" viewBox="0 0 40 40" aria-hidden="true"><circle cx="20" cy="20" r="18" fill="#2a8fd0"/><circle cx="20" cy="20" r="18" fill="none" stroke="#e07a20" stroke-width="3"/></svg>
<div class="abs svc-title" style="left:685px;top:769px">Management</div>
<p class="abs para" style="left:685px;top:795px;width:220px">Lorem Ipsum is simply dummy text of the printing and typesetting industry. Lorem Ipsum has been the industry's standard dummy text ever</p>

<div class="abs footer"></div>
<div class="abs vline" style="left:333px"></div>
<div class="abs vline" style="left:530px"></div>
<div class="abs vline" style="left:742px"></div>

<div class="abs heading" style="left:136px;top:898px;font-size:17px">Partners</div>
<p class="abs para" style="left:136px;top:936px;width:180px">Lorem Ipsum is simply dummy text of the printing and typesetting industry. Lorem Ipsum has been the industry's</p>
<p class="abs para" style="left:136px;top:984px;width:95px">Lorem Ipsum is simply dummy text of the printing and typesetting industry.</p>
<div class="abs badge" style="left:235px;top:989px;width:80px;height:57px"></div>
<svg class="abs" style="left:288px;top:1056px" width="30" height="14" viewBox="0 0 30 14" aria-hidden="true"><circle cx="6" cy="7" r="5.5" fill="#3d6e9a"/><path d="M8 4 L5 7 L8 10" stroke="#fff" fill="none" stroke-width="1.3"/><circle cx="22" cy="7" r="5.5" fill="#111"/><path d="M20 4 L23 7 L20 10" stroke="#fff" fill="none" stroke-width="1.3"/></svg>

<div class="abs heading" style="left:353px;top:898px;font-size:17px">Support</div>
<p class="abs para" style="left:353px;top:936px;width:163px">Lorem Ipsum is simply dummy text of the printing and typesetting industry. Lorem Ipsum has been the</p>
<p class="abs para" style="left:353px;top:984px;width:74px">Lorem Ipsum is simply dummy text of the printing and</p>
<div class="abs" style="left:436px;top:986px;width:80px;height:58px;border:1px solid #fff;background:linear-gradient(135deg,#8fb0c8,#e8c9a0 55%,#f2e6d4)" role="img" aria-label="Photo of a support agent wearing a headset"></div>
<div class="abs readmore" style="left:461px;top:1057px">Read More »</div>

<div class="abs heading" style="left:549px;top:898px;font-size:17px">Quick Contact</div>
<div class="abs input" style="left:547px;top:936px;width:178px;height:22px">Name</div>
<div class="abs input" style="left:547px;top:964px;width:178px;height:22px">E-mail</div>
<div class="abs input" style="left:547px;top:992px;width:178px;height:46px;padding-top:12px">Comment</div>
<div class="abs submit" style="left:647px;top:1048px;width:77px;height:20px">Submit</div>

<div class="abs heading" style="left:758px;top:898px;font-size:17px">Quick Links</div>
<ul class="abs qlist" style="left:758px;top:929px">
  <li>Home</li><li>About Us</li><li>Solutions</li><li>Careers</li><li>Services</li><li>Contact Us</li>
</ul>

<div class="abs bottom"></div>
<div class="abs copy">2012 © - VSI. All Rights Reserved<br>Powerd by : Brightforge Web</div>
<div class="abs tollfree">Toll-free- 488-70-321</div>
<div class="abs social" style="left:773px"></div>
<div class="abs social" style="left:809px"></div>
<div class="abs social" style="left:844px"></div>
<div class="abs social" style="left:879px"></div>
</body>
</html>
```